Request for Business Card Design

Hi. My name is Marlene, I am looking for a new business card design for my company, Quarrow Signal Instruments, LLC. I really like the design you did for Tarsel Venture and was hoping you could do something similar using our full logo and our mark. I am also open to any raised texture design using our mark. I have attached our full logo, which would need to be somewhere on the card, as well as the mark in both outline and full form, as well as our brand colors / guide. The card does not have to be white, as long as our logo and mark appear. I actually like darker colored business cards more, but am open to all options. If you are interested in working with me, please let me know. We would also take the business card design into letterhead design if you can do that.

```html
<!DOCTYPE html>
<html lang="en">
<head>
<meta charset="utf-8">
<title>Quarrow Signal Instruments – Business Card</title>
<link href="https://fonts.googleapis.com/css2?family=Open+Sans:wght@400;600;700&display=swap" rel="stylesheet">
<style>
  :root {
    --backdrop: #232325;
    --card: #202024;
    --edge: #1a9bd0;
    --accent: #1a9bd0;
    --ink: #ffffff;
    --emboss: #141416;
    --muted: #3a3a3f;
    --raised-light: #45454b;
    --raised-dark: #0b0b0d;
  }
  * { margin: 0; padding: 0; box-sizing: border-box; }
  html, body {
    width: 1200px; height: 780px; overflow: hidden;
    background: var(--backdrop);
    font-family: "Open Sans", Arial, sans-serif;
  }
  .stage {
    position: relative; width: 1200px; height: 780px;
    display: flex; align-items: center; justify-content: center; gap: 40px;
  }
  .card {
    position: relative; width: 540px; height: 309px; overflow: hidden;
    background: var(--card);
    border-bottom: 4px solid var(--edge);
    border-left: 4px solid var(--edge);
    box-shadow: 0 18px 36px rgba(0,0,0,.55);
  }

  /* Back side */
  .card-back { display: flex; align-items: center; justify-content: center; }
  .back-brand {
    display: flex; align-items: center; gap: 14px; white-space: nowrap;
    color: var(--emboss); font-weight: 700;
    font-size: 22px; letter-spacing: 1px; text-transform: uppercase;
    text-shadow: 0 1px 0 rgba(255,255,255,.06);
  }
  .back-brand .brand-dot {
    width: 32px; height: 32px; border-radius: 50%; background: var(--emboss); flex: none;
  }

  /* Front side */
  .front-brand {
    position: absolute; left: 30px; top: 36px;
    display: flex; align-items: center; gap: 10px; white-space: nowrap;
  }
  .front-brand .brand-dot {
    width: 28px; height: 28px; border-radius: 50%; background: var(--accent); flex: none;
  }
  .front-brand .brand-name {
    color: var(--muted); font-weight: 700; font-size: 14px;
    letter-spacing: .5px; text-transform: uppercase;
  }
  .holder {
    position: absolute; right: 28px; top: 26px; text-align: right;
  }
  .holder-name { color: var(--accent); font-weight: 700; font-size: 30px; line-height: 1; }
  .holder-role { color: var(--ink); font-weight: 600; font-size: 13px; margin-top: 4px; }
  .holder-bar {
    position: absolute; right: 0; top: 24px; width: 14px; height: 46px; background: var(--accent);
  }
  .raised-texture {
    position: absolute; right: 24px; top: 98px; width: 190px; height: 190px;
    border-radius: 50%;
    background: radial-gradient(circle at 35% 28%, var(--raised-light), var(--raised-dark) 72%);
    box-shadow: 0 6px 14px rgba(0,0,0,.5);
  }
  .address {
    position: absolute; left: 36px; top: 166px;
    color: var(--ink); font-size: 13px; line-height: 1.35;
  }
  .contacts {
    position: absolute; left: 36px; top: 210px; list-style: none;
    color: var(--ink); font-size: 12.5px; line-height: 1.45;
  }
  .contacts li { display: flex; align-items: center; gap: 8px; }
  .contacts svg { width: 12px; height: 12px; fill: var(--accent); flex: none; }
</style>
</head>
<body>
<main class="stage">
  <section class="card card-back" aria-label="Card back">
    <div class="back-brand"><span class="brand-dot"></span><span>Quarrow Signal Instruments</span></div>
  </section>

  <section class="card card-front" aria-label="Card front">
    <div class="front-brand"><span class="brand-dot"></span><span class="brand-name">Quarrow Signal Instruments</span></div>

    <div class="holder-bar"></div>
    <div class="holder">
      <div class="holder-name">Marlene</div>
      <div class="holder-role">Director</div>
    </div>

    <div class="raised-texture" role="img" aria-label="Large raised brand texture area"></div>

    <p class="address">1180 Fennick Park Road •<br>Alder Falls, CO 80999</p>

    <ul class="contacts">
      <li><svg viewBox="0 0 24 24"><path d="M6.6 10.8a15 15 0 0 0 6.6 6.6l2.2-2.2c.3-.3.7-.4 1-.2 1.1.4 2.3.6 3.6.6.6 0 1 .4 1 1V20c0 .6-.4 1-1 1A17 17 0 0 1 3 4c0-.6.4-1 1-1h3.5c.6 0 1 .4 1 1 0 1.3.2 2.5.6 3.6.1.3 0 .7-.2 1z"/></svg>+001 555 010 4821</li>
      <li><svg viewBox="0 0 24 24"><path d="M6 3h10v5H6zM3 9h18v11H3zm4 3v2h2v-2zm4 0v2h2v-2zm4 0v2h2v-2zm-8 4v2h2v-2zm4 0v2h2v-2z"/></svg>+001 555 010 4822</li>
      <li><svg viewBox="0 0 24 24"><path d="M12 2a10 10 0 1 0 0 20 10 10 0 0 0 0-20zm0 2c1.2 1.5 2 3.6 2.2 6H9.8C10 7.6 10.8 5.5 12 4zm-2.2 8h4.4c-.2 2.4-1 4.5-2.2 6-1.2-1.5-2-3.6-2.2-6zM4.1 12h3.7c.1 2 .6 3.9 1.4 5.4A8 8 0 0 1 4.1 12zm0-2a8 8 0 0 1 5.1-5.4C8.4 6.1 7.9 8 7.8 10zm12.1 0c-.1-2-.6-3.9-1.4-5.4a8 8 0 0 1 5.1 5.4zm0 2h3.7a8 8 0 0 1-5.1 5.4c.8-1.5 1.3-3.4 1.4-5.4z"/></svg>www.quarrowsignal.example</li>
      <li><svg viewBox="0 0 24 24"><path d="M2 6h20v12H2zm2 2v.5l8 5 8-5V8l-8 5z"/></svg>info@quarrowsignal.example</li>
    </ul>
  </section>
</main>
</body>
</html>
```